Web Design for a Biotech Consulting Firm

We need a web site design for a new business based in Philadelphia called Verantel Dx. This is a consulting firm that will serve medical diagnostics industry, which is part of the life science/healthcare industry focusing on developing and marketing products that help in early detection, monitoring or management of diseases. Our consulting firm will help medical diagnostic companies to overcome key challenges in designing, evaluating and marketing new products.Our company name is Verantel Dx. Verantel is Latin word for "something" Dx represents diagnostics. The idea behind the name is that we help companies to transform the original, early product ideas ("nothing") into "something"; which is a product with full clinical utility that will help to improve health and well-being.The web site should use the visual feel of the logo (attached), be modern, simple and clean looking and represent creativity, innovation, scientific thinking and progress.
Updates

Wix Design is acceptable

Industry/Entity Type

Biotechnology

Coding

Coded - Design and coding required

Number of Pages Required

1 page

Font styles to use
Sans Serif

Requirements
Must have
• simple, clean look couple of pages
Should not have
• a lot of pages

```html
<!DOCTYPE html>
<html lang="en">
<head>
<meta charset="utf-8">
<title>Verantel Dx — Medical Diagnostics Consulting</title>
<link href="https://fonts.googleapis.com/css2?family=Nunito+Sans:wght@300;400;600;700&display=swap" rel="stylesheet">
<style>
:root{
  --blue:#1a7cf2;
  --ink:#2a2a2a;
  --muted:#9a9a9a;
  --rule:#d9d9d9;
  --soft:#f5f5f5;
  --dark:#141414;
  --white:#ffffff;
}
*{box-sizing:border-box;margin:0;padding:0}
html,body{width:1200px;height:3594px;overflow:hidden}
body{position:relative;font-family:"Nunito Sans",Arial,sans-serif;color:var(--ink);background:var(--white)}
.abs{position:absolute}
.brand{display:flex;align-items:center;gap:8px;font-size:15px;font-weight:600;color:var(--ink)}
.brand-mark{width:10px;height:10px;background:var(--blue)}

/* hero */
.hero{left:0;top:0;width:1200px;height:677px;background:linear-gradient(135deg,#1d2c48 0%,#33476a 35%,#5b5a5e 60%,#2a3550 100%)}
.hero-shade{left:0;top:0;width:1200px;height:677px;background:rgba(10,20,40,.35)}
.topbar{left:77px;top:31px;width:1046px;height:93px;background:var(--white)}
.topbar .brand{position:absolute;left:21px;top:36px}
.nav{position:absolute;top:34px;display:flex;gap:0;font-size:17px;color:#555}
.nav a{position:absolute;white-space:nowrap;color:#555;text-decoration:none}
.nav a.active{color:var(--blue)}
.btn{display:flex;align-items:center;justify-content:center;background:var(--blue);color:var(--white);font-weight:700;font-size:16px;outline:2px solid var(--blue);outline-offset:3px;border:none}
.btn.light{outline-color:var(--white)}
.quote-top{left:886px;top:22px;width:141px;height:48px;position:absolute}
.hero-title{left:0;width:1200px;top:240px;text-align:center;font-size:86px;font-weight:400;color:var(--blue);letter-spacing:-1px}
.hero-sub{left:0;width:1200px;top:338px;text-align:center;font-size:42px;color:var(--white);font-weight:400}
.hero-text{left:240px;width:720px;top:408px;text-align:center;font-size:15px;line-height:27px;color:var(--white);font-weight:600}
.hero-btn{left:530px;top:493px;width:140px;height:50px}

/* section heads */
.head{left:77px;width:1046px;text-align:center;font-size:35px;font-weight:400;color:var(--ink)}
.rule{left:77px;width:1046px;height:1px;background:var(--rule)}
.rule i{position:absolute;left:430px;top:-2px;width:187px;height:4px;background:var(--blue)}

/* offer */
.offer{width:333px;height:312px;padding:42px 31px}
.offer.featured{background:var(--blue);box-shadow:0 4px 14px rgba(26,124,242,.35)}
.offer .icon{width:82px;height:82px;border-radius:50%;background:var(--blue);display:flex;align-items:center;justify-content:center}
.offer.featured .icon{background:var(--white)}
.offer h3{margin-top:22px;font-size:23px;font-weight:400;color:var(--ink)}
.offer p{margin-top:14px;font-size:14.5px;line-height:26px;color:var(--muted);font-weight:300}
.offer.featured h3,.offer.featured p{color:var(--white)}

.photo{border-radius:0}

/* about */
.about-title{left:638px;top:1765px;font-size:38px;font-weight:400}
.about-text{left:638px;top:1830px;width:484px;font-size:14.5px;line-height:26px;color:var(--muted);font-weight:300}
.about-btn{left:641px;top:2082px;width:136px;height:50px}

/* news */
.news-bg{left:0;top:2188px;width:1200px;height:645px;background:var(--soft)}
.news{width:333px;height:396px;background:var(--white);border:1px solid #ececec}
.news .pic{height:188px}
.news h4{margin:24px 13px 0;font-size:16.5px;font-weight:600;color:var(--ink)}
.news p{margin:12px 13px 0;font-size:14.5px;line-height:26px;color:var(--muted);font-weight:300}
.news .meta{display:flex;justify-content:space-between;align-items:center;margin:10px 13px 0;padding-right:20px}
.news .more{display:flex;align-items:center;gap:10px;color:var(--blue);font-size:13.5px;font-weight:700}
.news .date{display:flex;align-items:center;gap:10px;font-size:14.5px;color:#555}

/* subscribe */
.sub-text{left:300px;width:600px;top:2976px;text-align:center;font-size:14.5px;line-height:26px;color:var(--muted);font-weight:300}
.field{top:3063px;width:219px;height:61px;border:1px solid #cfcfcf;display:flex;align-items:center;gap:12px;padding-left:12px;font-size:13px;color:#888}
.sub-btn{left:726px;top:3063px;width:219px;height:61px;background:var(--blue);color:var(--white);display:flex;align-items:center;justify-content:center;font-size:17px;font-weight:600}

/* footer */
.footer{left:0;top:3188px;width:1200px;height:346px;background:var(--dark)}
.footer .brand{position:absolute;left:0;width:1200px;top:104px;justify-content:center;color:var(--white);font-size:19px}
.footer-links{position:absolute;top:182px;left:0;width:1200px;text-align:center;color:var(--white);font-size:14.5px;font-weight:600;word-spacing:4px}
.socials{position:absolute;top:230px;left:499px;display:flex;gap:6px}
.socials span{width:47px;height:47px;border-radius:50%;background:var(--white)}
.socials span:first-child{background:var(--blue)}
.copy{left:0;top:3534px;width:1200px;height:60px;background:var(--blue);color:var(--white);font-size:13.5px;display:flex;align-items:center;justify-content:center;gap:4px}
.copy b{font-weight:700}
</style>
</head>
<body>

<section class="abs hero" role="img" aria-label="Medical team meeting around a table in a clinic"></section>
<div class="abs hero-shade"></div>

<header class="abs topbar">
  <div class="brand"><span class="brand-mark"></span>Verantel Dx</div>
  <nav class="nav">
    <a class="active" style="left:315px">Home</a>
    <a style="left:411px">About</a>
    <a style="left:510px">Services</a>
    <a style="left:630px">Blog</a>
    <a style="left:714px">Contact</a>
  </nav>
  <svg style="position:absolute;left:823px;top:34px" width="22" height="22" viewBox="0 0 22 22" fill="none" stroke="#1a7cf2" stroke-width="2"><circle cx="9" cy="9" r="7"/><line x1="14" y1="14" x2="20" y2="20"/></svg>
  <div class="btn quote-top">GET A QUOTE</div>
</header>

<h1 class="abs hero-title">Verantel Dx</h1>
<h2 class="abs hero-sub">Medical Diagnostics Consulting</h2>
<p class="abs hero-text">Lorem ipsum dolor sit amet, consectetur adipiscing elit, sed do eiusmod tempor incididunt ut labore et dolore magna aliqua. Ut&nbsp; nisi ut aliquip ex ea commodo consequat.</p>
<div class="abs btn light hero-btn">READ MORE</div>

<h2 class="abs head" style="top:722px">What We Offer</h2>
<div class="abs rule" style="top:781px"><i></i></div>

<div class="abs offer" style="left:77px;top:843px;padding-left:0">
  <div class="icon"><svg width="44" height="44" viewBox="0 0 44 44" fill="none" stroke="#fff" stroke-width="1.6"><rect x="6" y="10" width="32" height="22" rx="2"/><line x1="2" y1="35" x2="42" y2="35"/><path d="M22 6l8 3v7c0 5-4 8-8 9-4-1-8-4-8-9V9z"/><path d="M18 16l3 3 5-5"/></svg></div>
  <h3 style="padding-left:9px">Developement</h3>
  <p style="padding-left:2px">Lorem ipsum dolor sit amet,consectetur adipiscing elit, sed do eiusmod tempor incididunt ut labore.</p>
</div>
<div class="abs offer featured" style="left:434px;top:843px">
  <div class="icon"><svg width="44" height="44" viewBox="0 0 44 44" fill="none" stroke="#2a2a2a" stroke-width="1.6"><rect x="8" y="8" width="28" height="28" rx="2"/><circle cx="22" cy="19" r="7"/><line x1="15" y1="19" x2="29" y2="19"/><line x1="22" y1="12" x2="22" y2="26"/><line x1="13" y1="30" x2="31" y2="30"/></svg></div>
  <h3>Marketing</h3>
  <p>Lorem ipsum dol amet,consectetur adipiscing elit, sed do eiusmod tempor incididunt ut labore.</p>
</div>
<div class="abs offer" style="left:811px;top:843px;padding-left:0">
  <div class="icon"><svg width="44" height="44" viewBox="0 0 44 44" fill="none" stroke="#fff" stroke-width="1.6"><rect x="6" y="6" width="20" height="32" rx="2"/><rect x="9" y="10" width="14" height="6"/><circle cx="16" cy="25" r="5"/><line x1="32" y1="8" x2="32" y2="36"/><line x1="38" y1="8" x2="38" y2="36"/></svg></div>
  <h3 style="padding-left:17px">Monitoring</h3>
  <p style="padding-left:17px">Lorem ipsum dolor sit amet,consectetur adipiscing elit, sed do eiusmod tempor incididunt ut labore.</p>
</div>

<div class="abs photo" style="left:77px;top:1229px;width:1046px;height:468px;background:linear-gradient(120deg,#c9cdd0 0%,#e8e6e2 45%,#b9bec6 100%)" role="img" aria-label="Doctor shaking hands with a smiling couple"></div>

<div class="abs photo" style="left:77px;top:1771px;width:499px;height:364px;background:linear-gradient(135deg,#e6e9ee 0%,#c7ced8 55%,#7d8796 100%)" role="img" aria-label="Stethoscope resting on a laptop keyboard"></div>
<h2 class="abs about-title">About Verantel Dx</h2>
<p class="abs about-text">Lorem ipsum dolor sit amet, consectetur adipiscing elit, sed eiusmod tempor incididunt ut labore et dolore magna aliqua. Ut enim a minim veniam, quis nostrud exercitation ullamco laboris nisi ut aliquip ex ea commodo consequat. Duis aute irure dolor in reprehenderit voluptate velit esse cillum dolore eu fugiat nulla pariatur. Excepteur it occaecat cupidatat non proident, sunt in culpa qui officia deserunt mollit anim id est laborum. At vero eos et accusamus et iusto odio dignissimos ducimus qui blanditiis praesentium voluptatum deleniti.</p>
<div class="abs btn about-btn">GET A QUOTE</div>

<div class="abs news-bg"></div>
<h2 class="abs head" style="top:2244px">Recent News Update</h2>
<div class="abs rule" style="top:2302px"><i></i></div>

<article class="abs news" style="left:77px;top:2364px">
  <div class="pic" style="background:linear-gradient(135deg,#eef1f4,#c8d3de)" role="img" aria-label="Doctor consulting a patient"></div>
  <h4>Lorem ipsum consectetur adipiscing.</h4>
  <p>Lorem Ipsum is simply dummy text of the has been the industry's standard dummy text ever since the 1500s,</p>
  <div class="meta"><span class="more">READ MORE <svg width="24" height="10" viewBox="0 0 24 10" fill="none" stroke="#1a7cf2" stroke-width="1.4"><line x1="0" y1="5" x2="22" y2="5"/><path d="M18 1l4 4-4 4"/></svg></span><span class="date"><svg width="16" height="16" viewBox="0 0 16 16" fill="none" stroke="#555" stroke-width="1.2"><rect x="1.5" y="3" width="13" height="12"/><line x1="1.5" y1="6.5" x2="14.5" y2="6.5"/><line x1="5" y1="1" x2="5" y2="4"/><line x1="11" y1="1" x2="11" y2="4"/></svg>17.07.2019</span></div>
</article>
<article class="abs news" style="left:434px;top:2364px">
  <div class="pic" style="background:linear-gradient(135deg,#dfe9f2,#9fb8cf)" role="img" aria-label="Nurse caring for an elderly patient"></div>
  <h4>Lorem ipsum consectetur adipiscing.</h4>
  <p>Lorem Ipsum is simply dummy text of the has been the industry's standard dummy text ever since the 1500s,</p>
  <div class="meta"><span class="more">READ MORE <svg width="24" height="10" viewBox="0 0 24 10" fill="none" stroke="#1a7cf2" stroke-width="1.4"><line x1="0" y1="5" x2="22" y2="5"/><path d="M18 1l4 4-4 4"/></svg></span><span class="date"><svg width="16" height="16" viewBox="0 0 16 16" fill="none" stroke="#555" stroke-width="1.2"><rect x="1.5" y="3" width="13" height="12"/><line x1="1.5" y1="6.5" x2="14.5" y2="6.5"/><line x1="5" y1="1" x2="5" y2="4"/><line x1="11" y1="1" x2="11" y2="4"/></svg>17.07.2019</span></div>
</article>
<article class="abs news" style="left:790px;top:2364px">
  <div class="pic" style="background:linear-gradient(135deg,#e4e6ea,#a9b0ba)" role="img" aria-label="Three doctors reviewing a laptop"></div>
  <h4>Lorem ipsum consectetur adipiscing.</h4>
  <p>Lorem Ipsum is simply dummy text of the has been the industry's standard dummy text ever since the 1500s,</p>
  <div class="meta"><span class="more">READ MORE <svg width="24" height="10" viewBox="0 0 24 10" fill="none" stroke="#1a7cf2" stroke-width="1.4"><line x1="0" y1="5" x2="22" y2="5"/><path d="M18 1l4 4-4 4"/></svg></span><span class="date"><svg width="16" height="16" viewBox="0 0 16 16" fill="none" stroke="#555" stroke-width="1.2"><rect x="1.5" y="3" width="13" height="12"/><line x1="1.5" y1="6.5" x2="14.5" y2="6.5"/><line x1="5" y1="1" x2="5" y2="4"/><line x1="11" y1="1" x2="11" y2="4"/></svg>17.07.2019</span></div>
</article>

<h2 class="abs head" style="top:2890px">Subscribe Newsletter</h2>
<div class="abs rule" style="top:2948px"><i></i></div>
<p class="abs sub-text">Lorem ipsum dolor sit amet, consectetur adipiscing elit, sed do&nbsp; tempor incididunt ut laboris nisi ut aliquip ex ea commodo consequat.</p>
<div class="abs field" style="left:257px"><svg width="18" height="18" viewBox="0 0 18 18" fill="#777"><circle cx="9" cy="5" r="4"/><path d="M1 17c0-5 4-7 8-7s8 2 8 7z"/></svg>Name :</div>
<div class="abs field" style="left:491px"><svg width="18" height="14" viewBox="0 0 18 14" fill="none" stroke="#777" stroke-width="1.4"><rect x="1" y="1" width="16" height="12"/><path d="M1 1l8 7 8-7M1 13l6-6M17 13l-6-6"/></svg>Email :</div>
<div class="abs sub-btn">SUSCRIBE NOW</div>

<footer class="abs footer">
  <div class="brand"><span class="brand-mark"></span>Verantel Dx</div>
  <div class="footer-links">Home &nbsp;|&nbsp; About &nbsp;|&nbsp; Services &nbsp;|&nbsp; News &nbsp;|&nbsp; Contact</div>
  <div class="socials"><span></span><span></span><span></span><span></span></div>
</footer>
<div class="abs copy">Copyright © <b>Verantel Dx</b> - 2019 . All Right Reserved</div>

</body>
</html>
```